Emerging automotive detailing business

I am starting a small automotive detailing business in hopes of becoming a well-known detailer to work on high end cars. I would like a card to reflect the high quality and time I put into my work. The name of the company is Bright Crest Detailing. I feel like it represents racecars getting off the line at the drag strip as well as an innuendo of "Up the Ladder". I do minor paint correction such as clay barring, multi-step buffing and polishing, waxing, hand washes, etc. I am always striving to learn more and improve my work. My goal is to have total customer satisfaction. This is a female run business but I do not want it to be very girly. Elegant is okay! I have pictures of my personal wrenfield attached, they do not need to be incorporated but if you can think of a cool way to use 1 or all of them, go for it!

Target Market(s)

Anyone that owns a vehicle. Preferably high end vehicles such as Valtori, Castellverde and Morvani but I will also happily work on any car, truck or suv no matter what brand.

Industry/Entity Type

Automotive

Contact Information for Business Card

Bright Crest Detailing
Mira Tolland
4175 Quenhollow Rd
Ashmere PA 17492
Cell phone- call/text- 717-555-0148
email- brightcrestdetails@maildrop-example.com
Instagram: @brightcrestdetailing
Facebook: facebook.com/brightcrestdetailing

Requirements
Must have
• Business name, my name, address, phone number. Listing that I do minor paint correction such as clay barring, multi-step buffing and polishing, waxing, hand washes, interior cleaning, and more. (This last part was in nice to haves but I have realized that I do really want it, so I moved it to must haves.) I want something that is different and eye-catching to my customers. Some people have done this very well with cards already submitted to me, but a lot have not. I didn't mess with the "look and feel bars" much because because I am pretty open to the overall design as long as it is not your basic run of the mill design.
Nice to have
• Something car related. Maybe an appointment time/date line. I do not have a logo, but if you would like to design one and incorporate it, that would be amazing!
Should not have
• Purple and Pink colors. Boring, basic, normal card.

```html
<!DOCTYPE html>
<html lang="en">
<head>
<meta charset="utf-8">
<title>Bright Crest Detailing — Business Card</title>
<link rel="stylesheet" href="https://fonts.googleapis.com/css2?family=Source+Sans+3:wght@400;600;700&display=swap">
<style>
  :root {
    --backdrop: #161616;
    --backdrop-deep: #050505;
    --card-blue-top: #0b76c4;
    --card-blue-bottom: #0d4e95;
    --card-white: #ffffff;
    --ink-white: #ffffff;
    --ink-soft: rgba(255, 255, 255, 0.85);
    --rule-soft: rgba(255, 255, 255, 0.35);
    --brand-blue: #1a5cab;
    --ink-blue: #1b56a0;
  }
  * { box-sizing: border-box; margin: 0; padding: 0; }
  html, body {
    width: 1200px;
    height: 900px;
    overflow: hidden;
  }
  body {
    background: linear-gradient(180deg, var(--backdrop) 0%, var(--backdrop-deep) 100%);
    font-family: "Source Sans 3", "Myriad Pro", sans-serif;
    position: relative;
  }

  .card {
    position: absolute;
    top: 306px;
    height: 271px;
    border-radius: 10px;
    overflow: hidden;
  }

  /* Front: contact side */
  .card-front {
    left: 150px;
    width: 438px;
    background: linear-gradient(180deg, var(--card-blue-top) 0%, var(--card-blue-bottom) 100%);
    color: var(--ink-white);
  }
  .front-brand {
    position: absolute;
    left: 22px;
    top: 100px;
    width: 170px;
    text-align: center;
    font-weight: 600;
    color: var(--ink-white);
  }
  .front-brand .brand-main {
    display: block;
    font-size: 26px;
    line-height: 1;
    letter-spacing: -0.3px;
  }
  .front-brand .brand-sub {
    display: block;
    margin-top: 8px;
    font-size: 17px;
    letter-spacing: 7px;
    line-height: 1;
    padding-left: 7px;
  }
  .contact-block {
    position: absolute;
    left: 212px;
    top: 70px;
  }
  .contact-name {
    font-size: 17px;
    font-weight: 600;
    line-height: 1;
    margin-bottom: 11px;
  }
  .contact-address {
    font-size: 12.5px;
    line-height: 18px;
    margin-bottom: 10px;
  }
  .contact-list {
    list-style: none;
    font-size: 10.5px;
    line-height: 18px;
  }
  .contact-list li {
    display: flex;
    align-items: center;
    gap: 6px;
    white-space: nowrap;
  }
  .contact-list svg {
    width: 9px;
    height: 9px;
    flex: none;
    fill: var(--ink-white);
  }
  .services {
    position: absolute;
    left: 22px;
    right: 22px;
    bottom: 16px;
    padding-top: 8px;
    border-top: 1px solid var(--rule-soft);
    text-align: center;
    font-size: 9.5px;
    line-height: 13px;
    color: var(--ink-soft);
    letter-spacing: 0.2px;
  }

  /* Back: appointment side */
  .card-back {
    left: 608px;
    width: 441px;
    background: var(--card-white);
    color: var(--ink-blue);
  }
  .back-brand {
    position: absolute;
    left: 0;
    right: 0;
    top: 56px;
    text-align: center;
    font-weight: 600;
    color: var(--brand-blue);
  }
  .back-brand .brand-main {
    display: block;
    font-size: 36px;
    line-height: 1;
    letter-spacing: -0.3px;
  }
  .back-brand .brand-sub {
    display: block;
    margin-top: 10px;
    font-size: 24px;
    letter-spacing: 9px;
    padding-left: 9px;
    line-height: 1;
  }
  .appointment-title {
    position: absolute;
    left: 0;
    right: 0;
    top: 162px;
    text-align: center;
    font-size: 17px;
    font-weight: 600;
  }
  .appointment-row {
    position: absolute;
    left: 72px;
    display: flex;
    align-items: flex-end;
    font-size: 12px;
    font-weight: 600;
  }
  .appointment-row.date-row { top: 199px; }
  .appointment-row.time-row { top: 229px; }
  .row-label { width: 48px; }
  .fill-line {
    display: inline-block;
    height: 10px;
    border-bottom: 2px dotted var(--ink-blue);
    margin-bottom: 2px;
  }
  .date-row .fill-line { width: 247px; }
  .time-row .fill-line.am-line { width: 96px; margin-right: 8px; }
  .time-row .fill-line.pm-line { width: 98px; margin: 0 4px 2px 8px; }
</style>
</head>
<body>

  <section class="card card-front" aria-label="Business card front">
    <div class="front-brand">
      <span class="brand-main">Bright Crest</span>
      <span class="brand-sub">Detailing</span>
    </div>

    <div class="contact-block">
      <p class="contact-name">Mira Tolland</p>
      <p class="contact-address">4175 Quenhollow Rd<br>Ashmere PA 17492</p>
      <ul class="contact-list">
        <li>
          <svg viewBox="0 0 10 10" aria-hidden="true"><path d="M2 0.5 L3.6 2.6 L2.7 3.6 C3.3 4.9 4.9 6.6 6.4 7.3 L7.4 6.4 L9.5 8 L8.4 9.5 C4.5 9.3 0.8 5.5 0.5 1.6 Z"/></svg>
          call/text- 717-555-0148
        </li>
        <li>
          <svg viewBox="0 0 10 10" aria-hidden="true"><path d="M0.5 2 H9.5 V8 H0.5 Z M1.2 2.4 L5 5.3 L8.8 2.4 Z" fill-rule="evenodd"/></svg>
          brightcrestdetails@maildrop-example.com
        </li>
        <li>
          <svg viewBox="0 0 10 10" aria-hidden="true"><rect x="0.5" y="0.5" width="9" height="9" rx="1.5"/></svg>
          @brightcrestdetailing
        </li>
      </ul>
    </div>

    <p class="services">
      Minor Paint Correction · Clay Barring · Multi-Step Buffing &amp; Polishing<br>
      Waxing · Hand Washes · Interior Cleaning &amp; More
    </p>
  </section>

  <section class="card card-back" aria-label="Business card back">
    <div class="back-brand">
      <span class="brand-main">Bright Crest</span>
      <span class="brand-sub">Detailing</span>
    </div>

    <p class="appointment-title">Your Next Appointment is</p>

    <div class="appointment-row date-row">
      <span class="row-label">Date :</span>
      <span class="fill-line"></span>
    </div>
    <div class="appointment-row time-row">
      <span class="row-label">Time:</span>
      <span class="fill-line am-line"></span>
      <span>AM</span>
      <span class="fill-line pm-line"></span>
      <span>PM</span>
    </div>
  </section>

</body>
</html>
```